Greeting Card Design - Bright Hearts Open Pages

Hi there

Thank you for taking the time to read about this project.

The project is for a range of greeting cards for the gay and lesbian community. The brand is called "Bright Hearts Open Pages".

In this project I require four designs in total (designs for homosexual couples, two for men and two for women). The designs need to reflect the general concept of being in love.

I am looking for variety (fun and funky, as well as modern and classy - please design to your tastes and I will give feedback).

I will work with each designer closely and provide the words for the cards as the designs are developed.

Thank you for considering this project.
Updates

I'm currently having issues with the craft huddle website and it won't let me upload files to show the logo. I will do so as soon as the website allows me. Thanks

Target Market(s)

Gay and lesbian community.

Industry/Entity Type

Community

Requirements
Must have
• I am looking for variety in the range. I would like designs that are modern and classy range; and also designs that are fun and funky.
Nice to have
• Hand drawings are good for the fun range, so is colour.
The classy range can be symbolic (e.g. holding hands) or black and whites.
Should not have
• Please do not use rainbows or rainbow coloured font.

```html
<!DOCTYPE html>
<html lang="en">
<head>
<meta charset="utf-8">
<title>Bright Hearts Open Pages – My love card</title>
<link href="https://fonts.googleapis.com/css2?family=Sacramento&family=Reenie+Beanie&display=swap" rel="stylesheet">
<style>
  :root {
    --card-red: #c01f2f;
    --paper: #ffffff;
    --ink: #333333;
    --fold-line: #555555;
    --panel-edge: #3a3a3a;
    --photo-dark: #4a4a4a;
    --photo-mid: #8a8a8a;
    --photo-light: #b9b9bb;
  }
  html, body {
    margin: 0;
    padding: 0;
    width: 1200px;
    height: 798px;
    overflow: hidden;
    background: var(--paper);
  }
  .canvas {
    position: relative;
    width: 1200px;
    height: 798px;
  }
  /* Outside of the card */
  .card-outside {
    position: absolute;
    left: 16px;
    top: 18px;
    width: 556px;
    height: 764px;
    border: 1px solid var(--panel-edge);
    box-sizing: border-box;
    background: var(--paper);
    overflow: hidden;
  }
  .cover-photo {
    position: absolute;
    left: 0;
    top: 382px;
    width: 100%;
    height: 382px;
    background: linear-gradient(90deg, var(--photo-dark) 0%, var(--photo-mid) 30%, var(--photo-light) 55%, var(--photo-mid) 80%, var(--photo-dark) 100%);
  }
  .title-band {
    position: absolute;
    left: 0;
    top: 432px;
    width: 250px;
    height: 72px;
    background: var(--card-red);
  }
  .title {
    position: absolute;
    left: 42px;
    top: 440px;
    margin: 0;
    font-family: "Sacramento", cursive;
    font-weight: 400;
    font-size: 44px;
    letter-spacing: -1px;
    line-height: 1;
    white-space: nowrap;
    color: var(--paper);
  }
  .brand-seal {
    position: absolute;
    left: 232px;
    top: 416px;
    width: 100px;
    height: 100px;
    border-radius: 50%;
    background: var(--paper);
    display: flex;
    align-items: center;
    justify-content: center;
    text-align: center;
  }
  .brand-name {
    font-family: "Reenie Beanie", cursive;
    font-size: 18px;
    line-height: 0.95;
    color: var(--card-red);
    width: 78px;
  }
  /* Inside of the card */
  .card-inside {
    position: absolute;
    left: 631px;
    top: 18px;
    width: 556px;
    height: 764px;
    border: 16px solid var(--card-red);
    box-sizing: border-box;
    background: var(--paper);
  }
  .fold-line {
    position: absolute;
    left: 631px;
    top: 400px;
    width: 556px;
    border-top: 1px dashed var(--fold-line);
  }
  .message {
    position: absolute;
    left: 631px;
    top: 557px;
    width: 556px;
    margin: 0;
    text-align: center;
    font-family: "Reenie Beanie", cursive;
    font-size: 25px;
    line-height: 1;
    color: var(--ink);
  }
</style>
</head>
<body>
<main class="canvas">
  <section class="card-outside" aria-label="Card front">
    <div class="cover-photo" role="img" aria-label="Black and white photo of two people in jeans holding hands"></div>
    <div class="title-band"></div>
    <h1 class="title">My love...</h1>
    <div class="brand-seal"><span class="brand-name">Bright Hearts Open Pages</span></div>
  </section>
  <section class="card-inside" aria-label="Card inside"></section>
  <div class="fold-line"></div>
  <p class="message">You are my favourite person in the world</p>
</main>
</body>
</html>
```